Corvanth Veylor - Advanced Skincare and undetectable Makeup for Men

We are in need of a professional webpage for our company Corvanth Veylor. We help every man feel his best by looking his best. Inspired by the myth of Corvanth, we offer makeup and skincare products along with education upon their use. Our mission is to celebrate masculinity in all of its forms, regardless of age, race, sexual orientation, or assigned gender at birth.

The webpage would serve as our online store, as a place where our clients can learn about our brand, view our "How-to" video tutorials, and get product information. An online blog will also be hosted in order to keep clients up to date with news, updates, media mentions, etc.

The color schemes that we use are mostly Black and Gold, with Red accents. please keep in mind that this is a men's cosmetics line, and therefore should read powerful, sexy, confident and bold - all with a high end look and feel.

Think along the lines of brands like Lem Brisko, QDV, Belluti, etc.

our logo is included in the files attached. images and copy will be added in at a later time; hence, general images that fit the feel and filler text is encouraged.

The products to be sold include:
a face cleanser in a pump dispenser bottle (1 size)
a mask in a round jar container (1 size)
a moisturizer in a pump container 1 size)
a concealer in a click pen with a brush applicator (3 shades)
a liquid liner pen (4 shades)
a contouring palette (2 shade options)
a setting spray (single option)

Target Market(s)

Millennial Men

Industry/Entity Type

Beauty

Number of Pages Required

5+ page

Font styles to use
Serif

Colors
ec1f27
000000
faa54b

Requirements
Must have
• ur essential requirements are:
• 1) a stunning and engaging landing page that truly captures the ideals of sexuality, boldness and confidence.
• 2) an interactive and engaging online store that is easy to update / add product / information to.
• 3) Product pages supporting various toggling images of the product, a shade selection option, ingredient information, usage instructions, pricing, and a link to a "how to video" unique to each individual product.
• 4) dedicated space where all of the tutorials can be organized together
• 5) an organized Blog section, that would include a segment for a Q&A section for us to update as the brand grows, ongoing contests (that would be easily hidden if there are no contests running at the moment) as well as general news and updates segment.
• 6) an "about us" page, where our customers are able to learn about our story, inspirations, humanitarian efforts and philosophies in product contents and purity.
• 7) a contact us page, which would include social media links, contact email and telephone number as well as physical address to be updated upon launch.
• 8) discrete privacy policy, terms of use, and return policy links available at the bottom of every page
Nice to have
• 1) A posting forum where clients could post their looks using our products, or maybe a live stream of our Pictoval account.
• 2) a member sign in page so that we can collect and store customer information for faster check out, keep track of purchases attached to their email address (future loyalty program plans) and maintain an email database for email notifications and the such.

```html
<!DOCTYPE html>
<html lang="en">
<head>
<meta charset="utf-8">
<title>Corvanth Veylor — Skincare and Makeup for Men</title>
<link rel="stylesheet" href="https://fonts.googleapis.com/css2?family=Cinzel:wght@400;700&family=Playfair+Display:wght@400;700&family=Raleway:wght@400;500;600&display=swap">
<style>
  :root {
    --orange: #faa54b;
    --orange-deep: #f39a3c;
    --red: #ec1f27;
    --black: #000000;
    --ink: #333333;
    --muted: #777777;
    --line: #e3e3e3;
    --panel: #efefef;
    --white: #ffffff;
  }
  * { box-sizing: border-box; margin: 0; padding: 0; }
  html, body { width: 1200px; height: 2872px; overflow: hidden; }
  body { background: var(--white); font-family: "Raleway", Arial, sans-serif; color: var(--ink); position: relative; }

  /* Header */
  .site-header { position: absolute; left: 0; top: 0; width: 1200px; height: 168px; background: var(--white); }
  .header-rule { position: absolute; left: 0; top: 52px; width: 1200px; height: 1px; background: var(--line); }
  .utility { position: absolute; right: 40px; top: 8px; display: flex; gap: 22px; }
  .brand { position: absolute; left: 40px; top: 60px; width: 280px; text-align: center; }
  .brand-mark { width: 40px; height: 40px; border: 3px solid #8a6a3c; margin: 0 auto 14px; }
  .brand-name { font-family: "Cinzel", Georgia, serif; font-weight: 700; font-size: 17px; letter-spacing: 2px; color: #6b5130; white-space: nowrap; }
  .main-nav { position: absolute; right: 36px; top: 94px; display: flex; gap: 40px; list-style: none; }
  .main-nav li { font-size: 15px; font-weight: 500; letter-spacing: 1px; color: #555; }
  .main-nav li.current { color: var(--orange-deep); }

  /* Hero */
  .hero { position: absolute; left: 0; top: 168px; width: 1200px; height: 560px;
    background: linear-gradient(90deg, #4e6f86 0%, #d9c8b6 22%, #e8d7c6 40%, #f2c79a 62%, #f4ad66 100%); }
  .hero-copy { position: absolute; left: 690px; top: 200px; width: 490px; }
  .hero-title { font-family: "Playfair Display", Georgia, serif; font-weight: 700; font-size: 40px; letter-spacing: 1px; color: var(--orange); text-transform: uppercase; white-space: nowrap; }
  .hero-text { margin-top: 14px; width: 450px; font-size: 22px; line-height: 1.4; color: var(--white); }

  /* Features */
  .features { position: absolute; left: 0; top: 728px; width: 1200px; height: 272px; background: var(--white); }
  .feature { position: absolute; top: 84px; width: 240px; text-align: center; }
  .feature-icon { width: 68px; height: 68px; margin: 0 auto; border: 2px solid var(--line); border-radius: 50%; display: flex; align-items: center; justify-content: center; background: var(--white); }
  .feature-label { margin-top: 26px; font-size: 15px; font-weight: 500; letter-spacing: 1px; color: #444; text-transform: uppercase; }
  .feature-link { position: absolute; top: 118px; height: 2px; background: var(--line); }

  /* New products */
  .new-products { position: absolute; left: 0; top: 1000px; width: 1200px; height: 500px; background: var(--panel); }
  .section-title { font-family: "Playfair Display", Georgia, serif; font-weight: 700; color: var(--orange); text-transform: uppercase; letter-spacing: 1px; }
  .new-products .section-title { position: absolute; left: 76px; top: 60px; font-size: 42px; }
  .slider-arrows { position: absolute; right: 84px; top: 68px; display: flex; gap: 14px; }
  .slider-arrow { width: 34px; height: 34px; border: 2px solid var(--orange); background: var(--white); display: flex; align-items: center; justify-content: center; }
  .range-list { position: absolute; left: 76px; top: 156px; list-style: none; }
  .range-list li { font-size: 17px; color: #444; height: 37px; display: flex; align-items: center; }
  .range-list li::before { content: ""; width: 9px; height: 9px; border-radius: 50%; background: var(--red); margin-right: 22px; }
  .product-card { position: absolute; top: 148px; width: 208px; height: 312px; background: var(--white); border: 2px solid #dedede; overflow: hidden; }
  .product-card.featured { border-color: var(--orange); }
  .product-photo { position: absolute; left: 22px; top: 22px; width: 160px; height: 176px; }
  .ribbon { position: absolute; left: -34px; top: 14px; width: 130px; height: 26px; background: var(--red); color: var(--white); font-size: 13px; font-weight: 600; text-align: center; line-height: 26px; transform: rotate(-45deg); letter-spacing: 1px; }
  .product-name { position: absolute; left: 0; top: 218px; width: 100%; text-align: center; font-size: 14px; color: #444; }
  .product-card.muted .product-name { color: #999; }
  .cart-btn { position: absolute; left: 44px; top: 250px; width: 118px; height: 32px; border: 1.5px solid var(--red); color: var(--red); font-size: 13px; font-weight: 600; display: flex; align-items: center; justify-content: center; letter-spacing: 1px; }
  .cart-btn.primary { background: var(--red); color: var(--white); }
  .cart-btn.faded { border-color: #d0d0d0; color: #b0b0b0; }

  /* Promo banner */
  .promo { position: absolute; left: 0; top: 1536px; width: 1200px; height: 424px; background: linear-gradient(90deg, #ececec 0%, #f7f3ef 40%, #f3ebe4 100%); }
  .promo-model { position: absolute; left: 60px; top: 0; width: 320px; height: 424px; background: linear-gradient(180deg, #6d5542 0%, #d8b195 30%, #f4f1ee 62%, #e6e4e2 100%); }
  .promo-products { position: absolute; left: 830px; top: 70px; width: 280px; height: 330px; background: linear-gradient(135deg, #b8324a 0%, #7a2334 35%, #2e2e33 60%, #4f7fbf 100%); border-radius: 6px; }
  .promo-copy { position: absolute; left: 412px; top: 150px; width: 400px; }
  .promo-title { font-family: "Playfair Display", Georgia, serif; font-weight: 700; font-size: 34px; color: var(--orange); letter-spacing: 1px; text-transform: uppercase; white-space: nowrap; }
  .promo-offer { margin-top: 8px; font-size: 23px; color: #333; }
  .shop-btn { margin-top: 18px; width: 190px; height: 50px; background: var(--red); color: var(--white); font-family: "Playfair Display", Georgia, serif; font-weight: 700; font-size: 21px; letter-spacing: 1px; display: flex; align-items: center; justify-content: center; }

  /* Blog */
  .blog .section-title { position: absolute; left: 0; top: 2016px; width: 1200px; text-align: center; font-size: 42px; }
  .blog-card { position: absolute; top: 2092px; width: 500px; height: 336px; overflow: hidden; }
  .blog-photo { position: absolute; inset: 0; }
  .blog-caption { position: absolute; left: 0; bottom: 0; width: 100%; height: 92px; background: rgba(0,0,0,0.62); color: var(--white); font-size: 15px; line-height: 1.45; padding: 20px 90px 0 24px; }
  .blog-arrow { position: absolute; right: 22px; bottom: 20px; width: 52px; height: 52px; border-radius: 50%; background: var(--white); display: flex; align-items: center; justify-content: center; }

  /* Footer */
  .site-footer { position: absolute; left: 0; top: 2488px; width: 1200px; height: 384px; background: var(--orange); text-align: center; }
  .footer-brand { position: absolute; left: 0; top: 80px; width: 1200px; }
  .footer-brand .brand-mark { border-color: var(--black); width: 36px; height: 36px; margin-bottom: 14px; }
  .footer-brand .brand-name { color: var(--black); font-size: 19px; }
  .subscribe { position: absolute; left: 364px; top: 192px; width: 472px; height: 46px; border-radius: 23px; background: var(--white); border: 2px solid #6b4a22; }
  .subscribe-field { position: absolute; left: 24px; top: 12px; font-size: 14px; color: #888; }
  .subscribe-btn { position: absolute; right: -2px; top: -2px; width: 140px; height: 46px; border-radius: 23px; background: #4a2f12; color: var(--white); font-size: 14px; font-weight: 600; letter-spacing: 1px; display: flex; align-items: center; justify-content: center; }
  .footer-nav { position: absolute; left: 0; top: 264px; width: 1200px; display: flex; justify-content: center; gap: 16px; list-style: none; font-size: 15px; color: #3a2a18; }
  .footer-rule { position: absolute; left: 40px; top: 318px; width: 1120px; height: 1px; background: rgba(0,0,0,0.2); }
  .copyright { position: absolute; left: 0; top: 340px; width: 1200px; font-size: 13px; color: #3a2a18; }
</style>
</head>
<body>

<header class="site-header">
  <div class="utility">
    <svg width="22" height="22" viewBox="0 0 22 22" fill="none" stroke="#666" stroke-width="2"><circle cx="9" cy="9" r="6.5"/><line x1="14" y1="14" x2="20" y2="20"/></svg>
    <svg width="24" height="22" viewBox="0 0 24 22" fill="none" stroke="#666" stroke-width="2"><path d="M1 2h4l3 12h12l3-9H7"/><circle cx="10" cy="19" r="1.6"/><circle cx="18" cy="19" r="1.6"/></svg>
  </div>
  <div class="header-rule"></div>
  <div class="brand">
    <div class="brand-mark"></div>
    <div class="brand-name">CORVANTH VEYLOR</div>
  </div>
  <ul class="main-nav">
    <li class="current">HOME</li>
    <li>ABOUT</li>
    <li>PRODUCTS</li>
    <li>FAQ</li>
    <li>BLOG</li>
    <li>CONTACT US</li>
  </ul>
</header>

<section class="hero" role="img" aria-label="Man with a towel around his neck touching his smooth jaw after skincare">
  <div class="hero-copy">
    <h1 class="hero-title">Corvanth Veylor</h1>
    <p class="hero-text">Lorem Ipsum is simply dummy text of the printing and typesetting industry Lorem Ipsum.</p>
  </div>
</section>

<section class="features">
  <div class="feature-link" style="left:366px;width:190px;"></div>
  <div class="feature-link" style="left:630px;width:198px;"></div>
  <div class="feature" style="left:208px;">
    <div class="feature-icon">
      <svg width="34" height="26" viewBox="0 0 34 26" fill="var(--orange)"><rect x="1" y="3" width="19" height="14" rx="1"/><path d="M21 7h7l5 6v4h-12z"/><circle cx="8" cy="20" r="3.4"/><circle cx="26" cy="20" r="3.4"/></svg>
    </div>
    <div class="feature-label">Free Shipping</div>
  </div>
  <div class="feature" style="left:472px;">
    <div class="feature-icon">
      <svg width="30" height="30" viewBox="0 0 30 30" fill="var(--orange)"><circle cx="15" cy="10" r="7"/><path d="M2 29c1-8 6-11 13-11s12 3 13 11z"/></svg>
    </div>
    <div class="feature-label">Online Support</div>
  </div>
  <div class="feature" style="left:744px;">
    <div class="feature-icon">
      <svg width="32" height="32" viewBox="0 0 32 32"><circle cx="16" cy="16" r="14" fill="var(--orange)"/><text x="16" y="22" text-anchor="middle" font-family="Raleway, sans-serif" font-size="17" font-weight="700" fill="#fff">$</text></svg>
    </div>
    <div class="feature-label">Money Guarantee</div>
  </div>
</section>

<section class="new-products">
  <h2 class="section-title">New Products</h2>
  <div class="slider-arrows">
    <div class="slider-arrow"><svg width="12" height="14" viewBox="0 0 12 14"><path d="M9 1 3 7l6 6" fill="none" stroke="#333" stroke-width="2.4"/></svg></div>
    <div class="slider-arrow"><svg width="12" height="14" viewBox="0 0 12 14"><path d="M3 1l6 6-6 6" fill="none" stroke="#333" stroke-width="2.4"/></svg></div>
  </div>
  <ul class="range-list">
    <li>face cleanser</li>
    <li>Face mask</li>
    <li>Moisturizer</li>
    <li>Concealer pen with a brush</li>
    <li>applicator</li>
    <li>liquid liner pen</li>
    <li>contouring palette</li>
    <li>Setting spray</li>
  </ul>

  <article class="product-card featured" style="left:452px;">
    <div class="product-photo" role="img" aria-label="Red pump bottles of face cleanser" style="background:linear-gradient(180deg,#f7e6ea 0%,#d14a6a 45%,#9b2440 100%);"></div>
    <div class="ribbon">NEW</div>
    <div class="product-name">Lorem Ipsum is simply</div>
    <div class="cart-btn primary">ADD TO CART</div>
  </article>
  <article class="product-card" style="left:680px;">
    <div class="product-photo" role="img" aria-label="Black setting spray bottle" style="background:linear-gradient(180deg,#f4f4f4 0%,#8a8a8e 45%,#1e1e22 100%);"></div>
    <div class="ribbon">NEW</div>
    <div class="product-name">Lorem Ipsum is simply</div>
    <div class="cart-btn">ADD TO CART</div>
  </article>
  <article class="product-card muted" style="left:916px;">
    <div class="product-photo" role="img" aria-label="Blue round jar of face mask with applicator" style="background:linear-gradient(180deg,#f2f5fa 0%,#8fb0e0 45%,#3d6cb8 100%);"></div>
    <div class="product-name">Lorem Ipsum is simply</div>
    <div class="cart-btn faded">ADD TO CART</div>
  </article>
</section>

<section class="promo">
  <div class="promo-model" role="img" aria-label="Bearded man in a white shirt resting his chin on his hand"></div>
  <div class="promo-copy">
    <h2 class="promo-title">Corvanth Veylor</h2>
    <p class="promo-offer">Skin care for men -Off 35%</p>
    <div class="shop-btn">SHOP NOW</div>
  </div>
  <div class="promo-products" role="img" aria-label="Group of red, black and blue skincare bottles and jars"></div>
</section>

<section class="blog">
  <h2 class="section-title">Blog Post</h2>
  <article class="blog-card" style="left:80px;">
    <div class="blog-photo" role="img" aria-label="Man applying skincare in a bathroom mirror" style="background:linear-gradient(135deg,#7a8c9c 0%,#d8b59c 45%,#f1e6dc 70%,#b9c2c9 100%);"></div>
    <div class="blog-caption">Lorem Ipsum is simply dummy text of the printing and typesetting industry Lorem Ipsum.</div>
    <div class="blog-arrow"><svg width="22" height="20" viewBox="0 0 22 20"><path d="M2 10h16M11 3l7 7-7 7" fill="none" stroke="#111" stroke-width="3"/></svg></div>
  </article>
  <article class="blog-card" style="left:620px;">
    <div class="blog-photo" role="img" aria-label="Man washing his face at a sink" style="background:linear-gradient(135deg,#cfd6db 0%,#a98a76 40%,#5d4a40 70%,#e4e6e8 100%);"></div>
    <div class="blog-caption">Lorem Ipsum is simply dummy text of the printing and typesetting industry Lorem Ipsum.</div>
    <div class="blog-arrow"><svg width="22" height="20" viewBox="0 0 22 20"><path d="M2 10h16M11 3l7 7-7 7" fill="none" stroke="#111" stroke-width="3"/></svg></div>
  </article>
</section>

<footer class="site-footer">
  <div class="footer-brand">
    <div class="brand-mark"></div>
    <div class="brand-name">CORVANTH VEYLOR</div>
  </div>
  <div class="subscribe">
    <span class="subscribe-field">Enter Your Email</span>
    <span class="subscribe-btn">SUBSCRIBE</span>
  </div>
  <ul class="footer-nav">
    <li>Home</li><li>|</li><li>About</li><li>|</li><li>Products</li><li>|</li><li>FAQ</li><li>|</li><li>Blog</li><li>|</li><li>Contact</li>
  </ul>
  <div class="footer-rule"></div>
  <p class="copyright">© Corvanth Veylor Products, P.C. 2018 – All rights reserved | Privacy Policy | Terms &amp; Conditions</p>
</footer>

</body>
</html>
```